Corvin Ridge Software PowerPoint template

We are a software company selling endpoint visibility, access and security technology to enterprise-level IT departments.
Our technology helps organizations gain comprehensive visibility into and control over devices accessing their corporate network so they can quickly identify and address suspicious activity on the network that could lead to potential threats like data breaches.
This technology can cost organizations upwards of $1M - depending on the size of the organization. Our primary clients are Vestral 2,000 companies.
We want a professional, polished PowerPoint template that we can use for all company presentations. Please include:
Title page
Section page
General info page
Thank you page
Logo options and color specs are attached.
Please include our tagline on at least the title page: Discover the edge. Optimize the whole.
Reason: Seeking more options. Looking for a clean design that uses lots of white space.
Software

```html
<!DOCTYPE html>
<html lang="en">
<head>
<meta charset="utf-8">
<title>Corvin Ridge Software – Title Slide</title>
<link href="https://fonts.googleapis.com/css2?family=Oxygen:wght@300;400;700&display=swap" rel="stylesheet">
<style>
  :root {
    --brand-red: #8c1c20;
    --brand-copper: #d0815a;
    --text-grey: #7a7a7a;
    --text-dark-grey: #6a6a6a;
    --paper: #ffffff;
  }
  * { margin: 0; padding: 0; box-sizing: border-box; }
  html, body {
    width: 1200px;
    height: 849px;
    overflow: hidden;
    background: var(--paper);
  }
  .slide {
    position: relative;
    width: 1200px;
    height: 849px;
    background: var(--paper);
    font-family: "Oxygen", "Helvetica Neue", Arial, sans-serif;
  }
  .brand {
    position: absolute;
    left: 130px;
    top: 150px;
    display: flex;
    align-items: center;
    gap: 22px;
  }
  .brand-dot {
    width: 44px;
    height: 44px;
    border-radius: 50%;
    background: var(--brand-copper);
  }
  .brand-name {
    color: var(--brand-red);
    font-weight: 700;
    font-size: 34px;
    letter-spacing: 3px;
    text-transform: uppercase;
    line-height: 1;
  }
  .tagline {
    position: absolute;
    left: 128px;
    top: 358px;
    color: var(--brand-red);
    font-weight: 400;
    font-size: 66px;
    line-height: 77px;
    letter-spacing: -0.5px;
    text-transform: uppercase;
  }
  .presentee {
    position: absolute;
    left: 130px;
    top: 556px;
    color: var(--text-dark-grey);
    font-weight: 700;
    font-size: 22px;
    text-transform: uppercase;
  }
  .date {
    position: absolute;
    left: 130px;
    top: 594px;
    color: var(--text-grey);
    font-weight: 400;
    font-size: 20px;
    text-transform: uppercase;
  }
  .footer-url {
    position: absolute;
    left: 130px;
    top: 756px;
    color: var(--brand-red);
    font-size: 17px;
    font-weight: 400;
    text-transform: uppercase;
    letter-spacing: 0.2px;
  }
  .footer-url strong { font-weight: 700; }
  .footer-bar {
    position: absolute;
    left: 442px;
    top: 760px;
    width: 758px;
    height: 12px;
    background: var(--brand-copper);
  }
  .copyright {
    position: absolute;
    right: 56px;
    top: 781px;
    color: var(--text-dark-grey);
    font-size: 11px;
    font-weight: 700;
  }
</style>
</head>
<body>
  <main class="slide">
    <div class="brand">
      <span class="brand-dot"></span>
      <span class="brand-name">Corvin Ridge Software</span>
    </div>

    <h1 class="tagline">Discover the edge,<br>Optimize the whole</h1>

    <p class="presentee">Name of the presentee</p>
    <p class="date">Date : MM DD YY</p>

    <p class="footer-url">www. <strong>corvinridge</strong>software.com</p>
    <div class="footer-bar"></div>
    <p class="copyright">©2015 Corvin Ridge Software</p>
  </main>
</body>
</html>
```